professional business card design

Business card design. Photos have been uploaded and i am open to the designer choosing which photos to use. Would like the card to be mostyly in a grey scale design with black, whites, silver & grey colours. I have added copy of our flyer as would like on the back side of card our services to be listed. Do not use any bright colurs such as blue red green or yellow. i need to be able to edit the phone number and naem in the final card design submitted.

Target Market(s)

Clients

Industry/Entity Type

earhmovibng and transport

Contact Information for Business Card

Director Name, address, email, phone number and services

Colors

Designer to choose only greyscale colors for use in the design.

Requirements
Should not have
• no yellow, red, blue or green

```html
<!DOCTYPE html>
<html lang="en">
<head>
<meta charset="utf-8">
<title>Quarry Ridge Services – Business Card</title>
<link href="https://fonts.googleapis.com/css2?family=Arimo:wght@400;700&family=Ubuntu:wght@400;500;700&display=swap" rel="stylesheet">
<style>
  :root {
    --page-bg: #d8d4ce;
    --card-black: #0b0b0b;
    --steel-dark: #1a1a1a;
    --steel-mid: #2e2e2e;
    --silver-light: #f2f2f2;
    --silver-mid: #bdbdbd;
    --silver-dark: #8a8a8a;
    --text-white: #ffffff;
    --text-dark: #111111;
    --brand-grey: #a9a9a9;
  }
  * { margin: 0; padding: 0; box-sizing: border-box; }
  html, body { width: 900px; height: 1200px; overflow: hidden; }
  body { background: var(--page-bg); position: relative; font-family: "Arimo", Arial, sans-serif; }

  .card {
    position: absolute; left: 80px; width: 742px;
    border-radius: 30px; overflow: hidden;
    background: var(--card-black);
    box-shadow: 0 6px 14px rgba(0,0,0,.35);
  }
  .card--front { top: 132px; height: 440px; }
  .card--back  { top: 638px; height: 444px; }

  .metal-texture {
    position: absolute; left: 0; top: 0; width: 100%;
    background: radial-gradient(ellipse at 50% 35%, var(--steel-mid) 0%, var(--steel-dark) 55%, var(--card-black) 100%);
  }
  .card--front .metal-texture { height: 100%; }
  .card--back .metal-texture { height: 274px; }

  .brand-name {
    position: absolute; color: var(--brand-grey);
    font-family: "Ubuntu", Arial, sans-serif; font-weight: 700;
    line-height: 1; text-align: center;
  }
  .card--front .brand-name { left: 50px; top: 185px; width: 300px; font-size: 92px; letter-spacing: 4px; }

  .divider { position: absolute; left: 388px; top: 164px; width: 2px; height: 126px; background: var(--silver-light); }

  .holder-name { position: absolute; left: 418px; top: 156px; color: var(--text-white); font-weight: 700; font-size: 24px; letter-spacing: .5px; }
  .holder-title { position: absolute; left: 418px; top: 182px; color: var(--text-white); font-weight: 700; font-size: 16px; }

  .contact-list { position: absolute; left: 420px; top: 222px; list-style: none; }
  .contact-list li { display: flex; align-items: center; height: 23px; color: var(--text-white); font-size: 16px; }
  .contact-list svg { width: 14px; height: 14px; margin-right: 18px; fill: var(--text-white); }

  .silver-band {
    position: absolute; left: 0; width: 100%;
    background: linear-gradient(90deg, var(--silver-light) 0%, var(--silver-mid) 45%, var(--silver-light) 70%, var(--silver-dark) 100%);
    color: var(--text-dark); font-weight: 700;
  }
  .depot-band { top: 334px; height: 38px; font-size: 17px; line-height: 38px; padding-left: 58px; letter-spacing: .3px; }

  .card--back .brand-name { left: 0; width: 742px; top: 60px; font-size: 150px; letter-spacing: 8px; }
  .brand-suffix { position: absolute; left: 0; width: 742px; top: 220px; text-align: center; color: var(--brand-grey); font-family: "Ubuntu", Arial, sans-serif; font-weight: 700; font-size: 32px; }

  .services-band { top: 274px; height: 44px; text-align: center; font-size: 24px; line-height: 44px; font-weight: 500; font-family: "Ubuntu", Arial, sans-serif; }

  .services-list { position: absolute; left: 0; top: 330px; width: 100%; font-family: "Ubuntu", Arial, sans-serif; color: var(--text-white); font-size: 15px; text-align: center; }
  .services-list p { height: 26px; line-height: 26px; word-spacing: 1px; }
  .services-list .sep { margin: 0 10px; font-size: 18px; }
</style>
</head>
<body>

<section class="card card--front">
  <div class="metal-texture" role="img" aria-label="Dark perforated metal texture"></div>
  <div class="brand-name">QRS</div>
  <div class="divider"></div>
  <h1 class="holder-name">DANIEL FERRIS</h1>
  <p class="holder-title">Director</p>
  <ul class="contact-list">
    <li><svg viewBox="0 0 16 16" aria-hidden="true"><path d="M2 5c0-2 3-3 6-3s6 1 6 3v1h-3V5H5v1H2zM3 7h10l1 6H2z"/></svg>000 444 000</li>
    <li><svg viewBox="0 0 16 16" aria-hidden="true"><path d="M1 4h14v9H1zM2 5l6 4 6-4" stroke="#0b0b0b" stroke-width="1"/></svg>info@quarryridgeservices.com.au</li>
    <li><svg viewBox="0 0 16 16" aria-hidden="true"><circle cx="8" cy="8" r="7"/><path d="M3 6c2 0 3 1 3 3s2 2 2 4M10 2c0 2 2 3 4 3" stroke="#0b0b0b" stroke-width="1.4" fill="none"/></svg>www.websiteaddress.com.au</li>
  </ul>
  <div class="silver-band depot-band">DEPOT :QRS LOT 114, RIDGE QUARRY ROAD, DUNMORE FLAT, AUSTRALIA</div>
</section>

<section class="card card--back">
  <div class="metal-texture" role="img" aria-label="Dark perforated metal texture"></div>
  <div class="brand-name">QRS</div>
  <div class="brand-suffix">Pty Ltd</div>
  <h2 class="silver-band services-band">OUR SERVICES</h2>
  <div class="services-list">
    <p>Mine site accredited equipment &amp; oparetors<span class="sep">|</span>Drop Deck Trailers<span class="sep">|</span>Road train flat tops</p>
    <p>Road train Tankers<span class="sep">|</span>Road train Trippers<span class="sep">|</span>Send &amp; Metal Supply &amp; cartage<span class="sep">|</span>Earthworks</p>
    <p>Road Building / Maintenance<span class="sep">|</span>potable water delivers<span class="sep">|</span>Heavy Vehicle Recovery services</p>
    <p>Over size load / Hot Shot Load</p>
  </div>
</section>

</body>
</html>
```